Newyear letter A4 or A5 to be sent to our historic clients and prospects.

We have a poem, and want to create a new years card to remind our clients of our product range and wish them a merry Christmas and a happy new year. This brief is for a brand of high end dog fashion.
Product image can be found here: https://files.plorvenshare.example/sh/q7mz2wd0xk4tb8n/KQTV9pLwenRa3H-MuXcDfYoJ?dl=0
Our website: www.marvelo.eu
The poem: https://notes.tavrikdocs.example/document/d/7Rk2_PWQzuvbLe8Tnd4HcXa_mGyo0sVqJ3kfwe9nbPX/edit?usp=sharing

B2B Pet businesses: Pet boutiques, Retail chaines, Wholesalers, Distributors

Product

Must have
• - Contain images from our collection
• - logo and baseline
• - Make the products pop

```html
<!DOCTYPE html>
<html lang="en">
<head>
<meta charset="utf-8">
<title>Marvelo – Season's Greetings</title>
<link rel="stylesheet" href="https://fonts.googleapis.com/css2?family=Open+Sans:wght@400&family=Libre+Caslon+Text&family=Great+Vibes&display=swap">
<style>
  :root {
    --paper: #efedec;
    --ink: #363636;
    --taupe: #9b978d;
    --rule: #a8a49b;
    --script: #a48d73;
    --brand-red: #e2262b;
    --holly-light: #dfe6da;
    --holly-mid: #b9cdb0;
    --photo-light: #d9d3ce;
    --photo-dark: #4a3830;
  }
  * { margin: 0; padding: 0; box-sizing: border-box; }
  html, body {
    width: 816px; height: 1200px; overflow: hidden;
    background: var(--paper);
  }
  .card {
    position: relative; width: 816px; height: 1200px;
    background: var(--paper);
    font-family: "Open Sans", sans-serif;
    color: var(--ink);
  }
  .greenery-top {
    position: absolute; left: 0; top: 0; width: 560px; height: 150px;
    background: linear-gradient(90deg, var(--holly-mid), var(--holly-light) 60%, var(--paper));
  }
  .greenery-side {
    position: absolute; left: 0; top: 150px; width: 90px; height: 200px;
    background: linear-gradient(180deg, var(--holly-light), var(--paper));
  }
  .greenery-corner {
    position: absolute; right: 0; bottom: 0; width: 322px; height: 100px;
    background: linear-gradient(90deg, var(--paper), var(--holly-light) 40%, var(--holly-mid));
  }
  .greeting {
    position: absolute; left: 37px; top: 370px; width: 373px; text-align: center;
  }
  .greeting-merry {
    font-family: "Libre Caslon Text", serif; font-weight: 400; color: var(--taupe);
    font-size: 42px; line-height: 50px; letter-spacing: 1px;
  }
  .greeting-christmas {
    font-family: "Libre Caslon Text", serif; color: var(--taupe);
    font-size: 55px; line-height: 62px;
  }
  .greeting-rule {
    height: 2px; background: var(--rule); margin-top: 16px;
  }
  .greeting-newyear {
    font-family: "Great Vibes", cursive; color: var(--script);
    font-size: 40px; line-height: 50px; margin-top: 22px;
    margin-right: 20px;
  }
  .product-photo {
    position: absolute; left: 0; top: 667px; width: 434px; height: 484px;
    background: linear-gradient(180deg, var(--photo-light), var(--photo-dark));
  }
  .poem {
    position: absolute; left: 444px; top: 122px; width: 360px;
    font-size: 17px; line-height: 26.2px;
  }
  .poem p + p { margin-top: 26px; }
  .brand {
    position: absolute; left: 440px; top: 985px; width: 310px;
    z-index: 2; text-align: center; white-space: nowrap;
    font-family: "Open Sans", sans-serif; font-weight: 400;
    color: var(--brand-red); font-size: 66px; line-height: 90px;
  }
</style>
</head>
<body>
<main class="card">
  <div class="greenery-top" role="img" aria-label="Watercolour holly, berries and pine branches"></div>
  <div class="greenery-side" role="img" aria-label="Watercolour twigs with red berries"></div>
  <div class="greenery-corner" role="img" aria-label="Watercolour holly and berry sprigs"></div>

  <section class="greeting">
    <h1 class="greeting-merry">MERRY</h1>
    <div class="greeting-christmas">CHRISTMAS</div>
    <div class="greeting-rule"></div>
    <div class="greeting-newyear">&amp; Happy New Year</div>
  </section>

  <div class="product-photo" role="img" aria-label="Product photo: small dog sitting in a brown fur-lined carrier bag"></div>

  <article class="poem">
    <p>This time for Christmas season come,<br>A time for Christmas season come,<br>A time for celebration!<br>For feasts, for gifts, for warm spiced rum,<br>For carols and elation.</p>
    <p>At Marvelo's we've all been busy,<br>Making gifts for special pets.<br>'nough baskets to make you dizzy,<br>Blankets, carriers and jackets.</p>
    <p>We hope your pets are snug and warm,<br>In their brand new Marvelo's ware.<br>Away from blistering winter storms,<br>Without worry or a care!</p>
    <p>And now, I think, our time is here,<br>To extend you many thanks.<br>Our hearts are filled with joyful cheer,<br>To have you in our ranks!</p>
    <p>With many changes to our sector,<br>It's a wonderful affair,<br>Announcing our new director,<br>Welcome, Lieke Vandermeer!</p>
    <p>But for now, we will say goodbye,<br>And leave you to your fun.<br>To your stockings and Christmas pies...<br>Happy Holidays everyone!</p>
  </article>

  <div class="brand">Marvelo</div>
</main>
</body>
</html>
```